Tall ridge firewood

It a new firewood outlet in Jindabyne nsw that will only sell top hardwood firewood (ironbark , red gum, grey gum, an box mix. I would like to see a web page the we can do order online payment for delivery. It will all so need to have photos of the firewood. I all so have logo for tall ridge firewood
Must have a modem look but easy to use I would like to see a black back ground of some sort.

Here are some other firewood web pages for ideas and firewood info
http://www.example-logpile.com.au
http://www.example-stackwood.com.au
http://www.example-splitlog.com.au
http://www.example-kendaltimber.com.au/firewood

Industry/Entity Type

Firewood

```html
<!DOCTYPE html>
<html lang="en">
<head>
<meta charset="utf-8">
<title>Tall Ridge Firewood</title>
<link rel="stylesheet" href="https://fonts.googleapis.com/css2?family=Oswald:wght@500;600&family=Open+Sans:wght@400;600;700&family=Arimo:wght@400;700&display=swap">
<style>
:root{
  --bg-dark:#141414;
  --blue:#1f72c0;
  --ink:#222;
  --body-text:#666;
  --white:#fff;
  --nav-active:#2b2b2b;
  --footer:#333333;
  --line:#d9d9d9;
}
*{box-sizing:border-box;margin:0;padding:0}
html,body{width:1093px;height:1200px;overflow:hidden}
body{
  position:relative;
  font-family:"Open Sans",Arial,sans-serif;
  background:linear-gradient(90deg,#101010,#1c1c1c 20%,#121212 45%,#1d1d1d 70%,#0f0f0f);
  color:var(--white);
}
.abs{position:absolute}

/* top bar */
.contact-line{left:150px;font-size:10px;color:var(--white);display:flex;align-items:center;gap:6px;white-space:nowrap}
.contact-line.call{top:20px}
.contact-line.mail{top:45px}
.call .number{font-family:"Oswald",sans-serif;font-size:18px;font-weight:600;letter-spacing:.2px}
.mail a{color:var(--white)}
.search{left:498px;top:28px;width:221px;height:26px;border:1px solid #888;border-radius:3px;background:#111;display:flex;overflow:hidden}
.search span{flex:1;font-size:10.5px;color:#bbb;padding:6px 8px;white-space:nowrap}
.search .go{width:26px;background:var(--blue);display:flex;align-items:center;justify-content:center}
.cart{right:147px;top:20px;font-size:10px;display:flex;align-items:center;gap:6px;white-space:nowrap}
.cart b{font-family:"Oswald",sans-serif;font-size:13px;font-weight:600}
.order-btn{left:851px;top:43px;width:95px;height:21px;border-radius:3px;background:linear-gradient(#fff,#d8d8d8);color:#111;font-size:10.5px;text-align:center;line-height:21px}

/* nav */
.main-nav{left:146px;top:92px;width:801px;height:32px;display:flex;background:var(--blue)}
.main-nav a{color:var(--white);font-family:"Arimo",sans-serif;font-size:10px;text-decoration:none;display:flex;align-items:center;justify-content:center;border-right:1px solid #2a80cf}
.main-nav a.active{background:var(--nav-active)}

/* page */
.page{left:146px;top:124px;width:801px;height:868px;background:var(--white)}
.hero-brand{left:0;top:0;width:322px;height:320px;display:flex;align-items:center;justify-content:center;gap:10px}
.brand-mark{width:22px;height:22px;border-radius:50%;background:var(--blue)}
.brand-name{font-family:"Open Sans",sans-serif;font-weight:700;font-size:20px;color:var(--ink);white-space:nowrap}
.hero-photo{left:322px;top:0;width:479px;height:320px;background:radial-gradient(circle at 40% 40%,#c79767,#8a5e36 55%,#5a3a20)}
.hero-rule{left:0;top:320px;width:801px;height:1px;background:var(--line)}

h2.title{font-family:"Oswald",sans-serif;font-weight:600;font-size:24px;color:#2d2d2d;line-height:1;white-space:nowrap}
h2.title em{font-style:normal;color:var(--blue)}
.welcome{left:25px;top:362px;width:418px}
.welcome p{font-family:"Arimo",sans-serif;font-size:10.4px;line-height:12.4px;color:var(--body-text);margin-top:16px}
.welcome p+p{margin-top:12px}
.v-divider{left:494px;top:363px;width:1px;height:194px;background:var(--line)}
.why{left:551px;top:362px;width:240px}
.why ul{list-style:none;margin-top:18px}
.why li{display:flex;gap:14px;align-items:center;margin-bottom:12px;font-family:"Arimo",sans-serif;font-size:10.2px;line-height:12.5px;color:var(--body-text)}
.tick{flex:0 0 19px;height:19px;border-radius:4px;background:#3a3a3a;display:flex;align-items:center;justify-content:center}
.btn-blue{display:inline-block;background:var(--blue);color:var(--white);font-size:10.5px;padding:4px 12px;border-radius:3px;margin-left:1px;margin-top:6px}
.section-rule{left:0;top:594px;width:801px;height:1px;background:var(--line)}

.products-head{left:25px;top:612px}
.view-all{left:716px;top:621px;font-size:10.5px;font-weight:700;color:var(--ink);text-decoration:underline}
.product{top:663px;width:162px;text-align:center}
.product .shot{width:162px;height:116px;border:1px solid #555}
.product h3{font-family:"Arimo",sans-serif;font-weight:400;font-size:14px;color:#333;margin-top:17px}
.product .price{font-family:"Oswald",sans-serif;font-weight:600;font-size:14px;color:var(--blue);margin-top:7px}
.arrow{top:693px}

/* footer */
.site-footer{left:146px;top:992px;width:801px;height:164px;background:var(--footer)}
.foot-col h4{font-family:"Open Sans",sans-serif;font-weight:700;font-size:10px;margin-bottom:10px}
.foot-col ul{list-style:none;font-family:"Arimo",sans-serif;font-size:10px;line-height:14.5px}
.foot-col li::before{content:"» ";margin-right:3px}
.foot-divider{top:24px;width:1px;height:118px;background:#555}
.socials{display:flex;gap:5px}
.socials span{width:24px;height:24px;background:var(--blue)}
.testimonial h4{font-size:15px;font-weight:700;margin-bottom:8px}
.testimonial p{font-family:"Arimo",sans-serif;font-size:10.2px;line-height:12.5px;color:#ddd}
.testimonial .who{margin-top:10px}
.btn-light{display:inline-block;margin-top:17px;background:linear-gradient(#fff,#d6d6d6);color:#111;font-size:10.5px;padding:4px 12px;border-radius:3px}
.copyright{left:146px;top:1156px;width:801px;height:32px;background:var(--blue);text-align:center;line-height:32px;font-size:10px}
.copyright b{font-weight:700}
</style>
</head>
<body>

<header>
  <div class="abs contact-line call">
    <svg width="12" height="14" viewBox="0 0 12 14"><path d="M3 1 L5 4 L4 6 Q5 9 7.5 10.5 L9 9.5 L11.5 11.5 L10 13.5 Q3 12 1 3 Z" fill="#aaa"/></svg>
    CALL US - <span class="number">5810 300 417</span>
  </div>
  <div class="abs contact-line mail">
    <svg width="12" height="9" viewBox="0 0 12 9"><rect x=".5" y=".5" width="11" height="8" fill="none" stroke="#aaa"/><path d="M.5 .5 L6 5 L11.5 .5" fill="none" stroke="#aaa"/></svg>
    EMAIL US - <a href="#">INFO@TALLRIDGEFIREWOOD.EXAMPLE</a>
  </div>
  <div class="abs search">
    <span>Find Firewood Products ..</span>
    <div class="go"><svg width="13" height="13" viewBox="0 0 13 13"><circle cx="5.5" cy="5.5" r="4" fill="none" stroke="#fff" stroke-width="2"/><path d="M8.5 8.5 L12 12" stroke="#fff" stroke-width="2.4"/></svg></div>
  </div>
  <div class="abs cart">
    <svg width="13" height="11" viewBox="0 0 13 11"><path d="M0 1 H2.5 L4 7 H11 L12.5 2.5 H3" fill="none" stroke="#ccc"/><circle cx="5" cy="9.5" r="1" fill="#ccc"/><circle cx="10" cy="9.5" r="1" fill="#ccc"/></svg>
    MY CART - <b>0 ITEM (S)</b>
  </div>
  <div class="abs order-btn">ORDER ONLINE</div>
</header>

<nav class="abs main-nav">
  <a class="active" style="width:100px">HOME</a>
  <a style="width:112px">ABOUT US</a>
  <a style="width:118px">PRODUCTS</a>
  <a style="width:129px">ACCESSORIES</a>
  <a style="width:114px">DELIVERY</a>
  <a style="width:98px">FAQ`S</a>
  <a style="width:130px;border-right:0">CONTACT US</a>
</nav>

<main class="abs page">
  <div class="abs hero-brand">
    <div class="brand-mark"></div>
    <div class="brand-name">Tall Ridge Firewood</div>
  </div>
  <div class="abs hero-photo" role="img" aria-label="Photo of a pile of cut hardwood logs"></div>
  <div class="abs hero-rule"></div>

  <section class="abs welcome">
    <h2 class="title"><em>Welcome to</em> Tall Ridge Firewood</h2>
    <p>Lorem ipsum dolor sit amet, consectetur adipisicing elit, sed do eiusmod tempor incididunt ut labore et dolore magna aliqua. Ut enim ad minim veniam, quis nostrud exercitation ullamco laboris nisi ut aliquip ex ea commodo consequat. Duis aute irure dolor in reprehenderit in voluptate velit esse cillum dolore eu fugiat nulla pariatur. Excepteur sint occaecat cupidatat non proident, sunt in culpa qui officia deserunt mollit anim id est laborum.</p>
    <p>Lorem ipsum dolor sit amet, consectetur adipisicing elit, sed do eiusmod tempor incididunt ut labore et dolore magna aliqua. Ut enim ad minim veniam, quis nostrud exercitation ullamco laboris nisi ut aliquip ex ea commodo consequat. Duis aute irure dolor in reprehenderit in voluptate velit esse cillum dolore eu fugiat nulla pariatur.</p>
  </section>
  <div class="abs v-divider"></div>
  <section class="abs why">
    <h2 class="title"><em>Why Choose</em> Us ?</h2>
    <ul>
      <li><span class="tick"><svg width="11" height="9" viewBox="0 0 11 9"><path d="M1 4.5 L4 7.5 L10 1" fill="none" stroke="#ccc" stroke-width="2"/></svg></span>Lorem ipsum dolor sit amet, consectetur adipisicing elit.</li>
      <li><span class="tick"><svg width="11" height="9" viewBox="0 0 11 9"><path d="M1 4.5 L4 7.5 L10 1" fill="none" stroke="#ccc" stroke-width="2"/></svg></span>Lorem ipsum dolor sit amet, consectetur adipisicing elit, sed do eiusmod tempor.</li>
      <li><span class="tick"><svg width="11" height="9" viewBox="0 0 11 9"><path d="M1 4.5 L4 7.5 L10 1" fill="none" stroke="#ccc" stroke-width="2"/></svg></span>Lorem ipsum dolor sit amet, consectetur adipisicing elit, sed do.</li>
    </ul>
    <span class="btn-blue">READ MORE</span>
  </section>
  <div class="abs section-rule"></div>

  <h2 class="abs title products-head"><em>Top Hardwood</em> Firewood Products</h2>
  <a class="abs view-all">VIEW ALL</a>

  <svg class="abs arrow" style="left:11px" width="14" height="56" viewBox="0 0 14 56"><path d="M13 1 L1 28 L13 55" fill="none" stroke="#ccc"/></svg>
  <svg class="abs arrow" style="left:776px" width="14" height="56" viewBox="0 0 14 56"><path d="M1 1 L13 28 L1 55" fill="none" stroke="#ccc"/></svg>

  <div class="abs product" style="left:35px">
    <div class="shot" role="img" aria-label="Photo of split ironbark firewood in a trailer" style="background:linear-gradient(#a0604a,#7a4a3a 60%,#555)"></div>
    <h3>Ironbark</h3><div class="price">$30.20 Only</div>
  </div>
  <div class="abs product" style="left:224px">
    <div class="shot" role="img" aria-label="Photo of split red gum firewood being handled" style="background:linear-gradient(120deg,#9a3a2a,#b44a38 55%,#333)"></div>
    <h3>Red Gum</h3><div class="price">$30.20 Only</div>
  </div>
  <div class="abs product" style="left:415px">
    <div class="shot" role="img" aria-label="Photo of a pile of grey gum logs" style="background:linear-gradient(#8a8f98,#5f646c)"></div>
    <h3>Grey Gum</h3><div class="price">$30.20 Only</div>
  </div>
  <div class="abs product" style="left:604px">
    <div class="shot" role="img" aria-label="Photo of box mix firewood burning in a fireplace" style="background:radial-gradient(circle at 50% 50%,#e0502a,#3a1a10 40%,#888 75%)"></div>
    <h3>Box Mix</h3><div class="price">$30.20 Only</div>
  </div>
</main>

<footer class="abs site-footer">
  <div class="abs foot-col" style="left:34px;top:24px">
    <h4>NAVIGATION</h4>
    <ul><li>Home</li><li>About Us</li><li>Products</li><li>Accessories</li><li>Delivery</li><li>Faq`s</li><li>Contact Us</li></ul>
  </div>
  <div class="abs foot-divider" style="left:149px"></div>
  <div class="abs foot-col" style="left:191px;top:24px">
    <h4>PRODUCTS</h4>
    <ul><li>Ironbark</li><li>Red gum</li><li>Grey gum</li><li>Box mix</li></ul>
  </div>
  <div class="abs foot-divider" style="left:287px"></div>
  <div class="abs foot-col" style="left:322px;top:24px">
    <h4>FOLLOW US ON</h4>
    <div class="socials" aria-label="Social links"><span></span><span></span><span></span><span></span></div>
  </div>
  <div class="abs foot-divider" style="left:473px"></div>
  <div class="abs testimonial" style="left:510px;top:18px;width:270px">
    <h4>Happy Client`s</h4>
    <p>Lorem ipsum dolor sit amet, consectetur adipisicing elit, sed do eiusmod tempor incididunt ut labore et dolore magna aliqua.</p>
    <p class="who"><b>Dana</b>. 15/06/13</p>
    <span class="btn-light">READ MORE</span>
  </div>
</footer>
<div class="abs copyright">COPYRIGHT © <b>TALL RIDGE FIREWOOD</b> 2013. ALL RIGHT RESERVED.</div>

</body>
</html>
```